Corporate Brochure for Exclusive Consultant Firm

Brochure needed for insurance adjusting firm. Our company is highly specialized in our field. Our target market are executives at insurance companies, insurance risk managers and insurance brokers. We specialize in industrial insurance claims in the mining, forestry, chemical plants, construction and legal liability sectors.

We are looking for a 8 1/2 x 11 bi-fold brochure that tells the story of our company. Our corporate colors are used. There is a place at the back for the pictures and short bios of the 3 people on our web site.

Refer to our web site for full details on our company. Please do not do cut and paste, we are looking for a creative, clean, professional design.

We want a brochure that we can send to the printer, so the necessary files for that. Also, we want the brochure to be in electronic form so we can distribute the brochure electronically.

www.harborlineclaims.example

Target Market(s)

Corporate executives

Industry/Entity Type

Insurance

Requirements
Must have
• clean, professional, modern look reflecting our website. Pictures of the 3 persons, short bio of each near the back. Can use photos from the site or use other files. Must provide files for print, and produce a digital version that we can share with clients electronically.
Nice to have
• COLORS: orange, light grey, white, black (to be used minimally, more as accent)
Should not have
• exact cut and paste from our website. We are looking for a clean modern and new brochure to market our business .

```html
<!DOCTYPE html>
<html lang="en">
<head>
<meta charset="utf-8">
<title>Harborline Claims Brochure</title>
<link href="https://fonts.googleapis.com/css2?family=Open+Sans:wght@400;600;700;800&display=swap" rel="stylesheet">
<style>
:root{
  --orange:#f0811f;
  --ink:#222;
  --band:#2a2a2a;
  --page:#f3f3f3;
}
*{box-sizing:border-box;margin:0;padding:0}
html,body{width:835px;height:1200px;overflow:hidden;background:var(--page);font-family:"Open Sans",Arial,sans-serif;color:var(--ink)}
.spread{position:absolute;left:28px;width:780px;height:588px;background:#fff;box-shadow:0 1px 4px rgba(0,0,0,.18)}
.spread.outside{top:6px}
.spread.inside{top:606px}
.panel{position:absolute;top:0;width:390px;height:100%;overflow:hidden}
.panel.left{left:0}
.panel.right{left:390px;border-left:1px solid #ddd}
.photo{position:absolute}
.small{font-size:6.2px;line-height:1.45;color:#555}
.logo{display:flex;align-items:center;gap:6px;font-weight:800;letter-spacing:1px;text-transform:uppercase}
.logo .mark{width:12px;height:12px;background:var(--orange)}
.logo .name{font-size:15px;color:var(--orange)}
/* outside left */
.map-band{left:0;top:0;width:390px;height:68px;background:linear-gradient(90deg,#3a3a3a,#8a8a8a 60%,#4a4a4a)}
.bio{position:absolute;left:14px;width:366px;display:flex;gap:10px}
.bio .portrait{width:54px;height:64px;background:linear-gradient(#9a9a9a,#5c5c5c);flex:none}
.bio .text{width:128px}
.bio .contact{width:160px;padding-left:10px}
.bio .contact p{margin-bottom:4px}
.bio .contact b{color:var(--ink)}
.footer-band{position:absolute;left:0;bottom:0;width:390px;height:64px;background:var(--band);display:flex;align-items:center;justify-content:center}
.footer-band .name{font-size:13px}
/* outside right */
.cover-logo{position:absolute;top:34px;left:0;width:100%;justify-content:center}
.cover-logo .name{font-size:20px}
.cover-photo{left:0;top:84px;width:390px;height:272px;background:linear-gradient(160deg,#1b2433 0%,#3a3020 45%,#c9700f 80%,#2a2218 100%)}
.cover-copy{position:absolute;left:150px;top:376px;width:225px}
.cover-copy h2{font-size:7.8px;font-weight:800;text-transform:uppercase;line-height:1.35;margin-bottom:6px}
.site-bar{position:absolute;left:150px;bottom:20px;width:225px;height:14px;background:var(--orange);color:#fff;font-size:6.5px;font-weight:700;display:flex;align-items:center;justify-content:flex-end;padding-right:8px}
/* inside left */
.sections{position:absolute;left:12px;top:16px;width:158px}
.sections h3{font-size:7.2px;font-weight:800;color:var(--orange);margin-bottom:1px}
.sections p{margin-bottom:8px}
.strips{position:absolute;left:165px;top:0}
/* inside right */
.inside-logo{position:absolute;top:22px;right:22px}
.inside-logo .name{font-size:16px}
.inside-photo{left:0;top:62px;width:390px;height:64px;background:linear-gradient(90deg,#c7c7c7,#7d7d7d 50%,#b9b9b9)}
.intro{position:absolute;left:150px;top:142px;width:225px}
.services{position:absolute;left:150px;top:206px;width:225px;list-style:none}
.services li{display:flex;align-items:center;gap:7px;font-size:10px;font-weight:700;color:var(--orange);margin-bottom:8px}
.services svg{flex:none}
.closing{position:absolute;left:150px;top:390px;width:225px}
.site-box{position:absolute;left:212px;bottom:26px;width:160px;height:16px;border:1px solid var(--orange);color:var(--orange);font-size:6.5px;font-weight:700;display:flex;align-items:center;justify-content:center}
</style>
</head>
<body>

<section class="spread outside">
  <div class="panel left">
    <div class="photo map-band" role="img" aria-label="Grey world map banner"></div>

    <div class="bio" style="top:88px">
      <div class="portrait" role="img" aria-label="Portrait photo of Daniel Mercer"></div>
      <p class="text small">Daniel Mercer has been leading industrial claim files for more than two decades, with deep focus on energy and chemical losses across the country and abroad.</p>
      <div class="contact small">
        <p>Certified senior adjuster with a long record in complex large loss work.</p>
        <p><b>E</b> dmercer@harborlineclaims.example<br><b>T</b> 555 010 2201<br><b>C</b> 555 010 2202</p>
      </div>
    </div>

    <div class="bio" style="top:206px">
      <div class="portrait" role="img" aria-label="Portrait photo of Owen Caldwell"></div>
      <p class="text small">Owen Caldwell is a senior partner of the firm who has adjusted major losses in the forest and mining sectors for leading insurers and brokers.</p>
      <div class="contact small">
        <p>Engineer and senior adjuster who guides the technical side of every major file.</p>
        <p><b>E</b> ocaldwell@harborlineclaims.example<br><b>T</b> 555 010 2203<br><b>C</b> 555 010 2204</p>
      </div>
    </div>

    <div class="bio" style="top:324px">
      <div class="portrait" role="img" aria-label="Portrait photo of Lena Ashford"></div>
      <p class="text small">Lena Ashford joined the firm after years as a risk manager and now heads commercial claims and litigation support services.</p>
      <div class="contact small">
        <p>Her practical view of loss control helps clients cut cost and speed up recovery.</p>
        <p><b>E</b> lashford@harborlineclaims.example<br><b>T</b> 555 010 2205<br><b>C</b> 555 010 2206</p>
      </div>
    </div>

    <div class="footer-band">
      <div class="logo"><span class="mark"></span><span class="name">Harborline Claims</span></div>
    </div>
  </div>

  <div class="panel right">
    <div class="logo cover-logo"><span class="mark"></span><span class="name">Harborline Claims</span></div>
    <div class="photo cover-photo" role="img" aria-label="Industrial plant lit up at night"></div>
    <div class="cover-copy">
      <h2>Technical expertise for<br>specialty insurance benefits</h2>
      <p class="small">Harborline Claims is a firm of highly skilled claims adjusters serving the insurance industry with a focus on large and complex industrial losses in energy, chemical, forest and mining operations.</p>
    </div>
    <div class="site-bar">www.harborlineclaims.example</div>
  </div>
</section>

<section class="spread inside">
  <div class="panel left">
    <div class="sections small">
      <h3>Our Approach</h3>
      <p>We bring a hands-on view to every file, working closely with insurers and brokers from first notice to final report.</p>
      <h3>Experience</h3>
      <p>Our team has adjusted thousands of industrial losses, giving clients sound judgement on even the most complex claims.</p>
      <h3>The Difference</h3>
      <p>Senior adjusters handle each file directly, so clients receive clear answers and steady contact at every stage.</p>
      <h3>Niche Expertise</h3>
      <p>We focus on energy, chemical, forest and mining risks where technical knowledge matters most.</p>
      <h3>Loss Control</h3>
      <p>We help insureds limit damage early, reducing the size of the loss and the time needed to restore operations.</p>
      <h3>Customer Service Tailored to Your Needs</h3>
      <p>Reports and updates follow the format each client prefers, delivered on time and in plain language.</p>
      <h3>Document Management</h3>
      <p>Secure digital files keep every record organised and available to clients whenever needed.</p>
    </div>
    <svg class="strips" width="225" height="588" viewBox="0 0 225 588" role="img" aria-label="Diagonal strips of industrial site photos">
      <defs>
        <linearGradient id="g1" x1="0" y1="0" x2="1" y2="1"><stop offset="0" stop-color="#8d8d8d"/><stop offset="1" stop-color="#3f3f3f"/></linearGradient>
        <linearGradient id="g2" x1="0" y1="0" x2="1" y2="1"><stop offset="0" stop-color="#b5b5b5"/><stop offset="1" stop-color="#5a5a5a"/></linearGradient>
      </defs>
      <polygon points="40,0 225,0 225,60 10,170" fill="url(#g1)"/>
      <polygon points="10,186 225,76 225,160 10,270" fill="url(#g2)"/>
      <polygon points="10,286 225,176 225,260 10,370" fill="url(#g1)"/>
      <polygon points="10,386 225,276 225,360 10,470" fill="url(#g2)"/>
      <polygon points="10,486 225,376 225,460 10,570" fill="url(#g1)"/>
      <polygon points="60,588 225,476 225,588" fill="url(#g2)"/>
    </svg>
  </div>

  <div class="panel right">
    <div class="logo inside-logo"><span class="mark"></span><span class="name">Harborline Claims</span></div>
    <div class="photo inside-photo" role="img" aria-label="Strip of grey industrial photos"></div>
    <p class="intro small">Whether complex industrial plants or mining operations, our adjusters deliver quality claims management backed by real technical knowledge in these core sectors:</p>
    <ul class="services">
      <li><svg width="12" height="12" viewBox="0 0 12 12"><path d="M2 6l3 3 5-6" fill="none" stroke="var(--orange)" stroke-width="2"/></svg>Energy</li>
      <li><svg width="12" height="12" viewBox="0 0 12 12"><path d="M2 6l3 3 5-6" fill="none" stroke="var(--orange)" stroke-width="2"/></svg>Chemical Operations</li>
      <li><svg width="12" height="12" viewBox="0 0 12 12"><path d="M2 6l3 3 5-6" fill="none" stroke="var(--orange)" stroke-width="2"/></svg>Forest Industry</li>
      <li><svg width="12" height="12" viewBox="0 0 12 12"><path d="M2 6l3 3 5-6" fill="none" stroke="var(--orange)" stroke-width="2"/></svg>Mining</li>
      <li><svg width="12" height="12" viewBox="0 0 12 12"><path d="M2 6l3 3 5-6" fill="none" stroke="var(--orange)" stroke-width="2"/></svg>Commercial Claims</li>
      <li><svg width="12" height="12" viewBox="0 0 12 12"><path d="M2 6l3 3 5-6" fill="none" stroke="var(--orange)" stroke-width="2"/></svg>Litigation Support Services</li>
    </ul>
    <p class="closing small">We are dedicated to quality and to the prompt, fair and economical settlement of claims. Our adjusters work closely with insurers, brokers and risk managers to deliver clear reports and reliable results on every file, large or small.</p>
    <div class="site-box">www.harborlineclaims.example</div>
  </div>
</section>

</body>
</html>
```